Working Capital graphics

Our business advisory firm requires 9 images to be re-created and improved in the branding of our business.

The 9 images have been uploaded below and the colours and branding of the business can be found at the website www.tallowmereadvisory.com.au

```html
<!DOCTYPE html>
<html lang="en">
<head>
<meta charset="utf-8">
<title>Working Capital Cycle</title>
<link rel="stylesheet" href="https://fonts.googleapis.com/css2?family=Jost:wght@500;600;700&display=swap">
<style>
  :root {
    --navy: #1b3a8a;
    --cyan: #0cb0f2;
    --orange: #f7941d;
    --wedge: #fb9322;
    --paper: #ffffff;
    --frame: #d6d6d6;
  }
  html, body { margin: 0; padding: 0; overflow: hidden; background: var(--paper); }
  .canvas { width: 1200px; height: 1166px; display: block; }
  .frame { fill: var(--paper); stroke: var(--frame); stroke-width: 5; }
  .spoke { stroke: var(--navy); stroke-width: 2; }
  .hub-ring { fill: var(--paper); stroke: var(--navy); stroke-width: 2; }
  .hub-core { fill: var(--cyan); }
  .hub-title { font-family: "Jost", sans-serif; font-weight: 600; font-size: 20px; fill: var(--paper); text-anchor: middle; letter-spacing: 0.5px; }
  .node circle { fill: var(--paper); stroke: var(--orange); stroke-width: 2.5; }
  .node text { font-family: "Jost", sans-serif; font-weight: 600; fill: var(--navy); text-anchor: middle; letter-spacing: 0.6px; }
  .node .sm { font-size: 7.5px; }
  .node .md { font-size: 9px; }
  .node .lg { font-size: 10.5px; }
  .cycle-label { font-family: "Jost", sans-serif; font-weight: 600; font-size: 18px; fill: var(--navy); text-anchor: middle; letter-spacing: 1px; }
  .wedge { fill: var(--wedge); }
  .wedge-divider { stroke: var(--paper); stroke-width: 2; fill: none; }
  .wedge-label { font-family: "Jost", sans-serif; font-weight: 500; font-size: 20px; fill: var(--paper); text-anchor: middle; letter-spacing: 2px; }
  .pointer { stroke: var(--navy); stroke-width: 3.5; fill: none; }
  .pointer-head { fill: var(--navy); }
</style>
</head>
<body>
<svg class="canvas" viewBox="0 0 1200 1166" xmlns="http://www.w3.org/2000/svg" role="img" aria-label="Working capital cycle: customer to cash, forecast to fulfillment, purchase to pay">
  <rect class="frame" x="2.5" y="2.5" width="1195" height="1161"/>

  <!-- Revenue management -->
  <g class="cycle revenue">
    <g class="spokes">
      <line class="spoke" x1="265" y1="269" x2="265" y2="118"/>
      <line class="spoke" x1="265" y1="269" x2="340" y2="138"/>
      <line class="spoke" x1="265" y1="269" x2="395" y2="193"/>
      <line class="spoke" x1="265" y1="269" x2="416" y2="268"/>
      <line class="spoke" x1="265" y1="269" x2="395" y2="343"/>
      <line class="spoke" x1="265" y1="269" x2="340" y2="399"/>
      <line class="spoke" x1="265" y1="269" x2="266" y2="419"/>
      <line class="spoke" x1="265" y1="269" x2="191" y2="399"/>
      <line class="spoke" x1="265" y1="269" x2="135" y2="344"/>
      <line class="spoke" x1="265" y1="269" x2="115" y2="269"/>
      <line class="spoke" x1="265" y1="269" x2="135" y2="194"/>
      <line class="spoke" x1="265" y1="269" x2="189" y2="139"/>
    </g>
    <circle class="hub-ring" cx="265" cy="269" r="97"/>
    <circle class="hub-core" cx="265" cy="269" r="87"/>
    <text class="hub-title" x="265" y="263">REVENUE</text>
    <text class="hub-title" x="265" y="285">MANAGEMENT</text>

    <g class="node" transform="translate(265 118)"><circle r="34"/><text class="md" y="-1">CUSTOMER<tspan x="0" dy="11">STRATEGY</tspan></text></g>
    <g class="node" transform="translate(340 138)"><circle r="34"/><text class="sm" y="-1">SALES<tspan x="0" dy="9">MANAGEMENT</tspan></text></g>
    <g class="node" transform="translate(395 193)"><circle r="34"/><text class="sm" y="-1">RISK<tspan x="0" dy="9">MANAGEMENT</tspan></text></g>
    <g class="node" transform="translate(416 268)"><circle r="34"/><text class="sm" y="-1">CONTRACT<tspan x="0" dy="9">MANAGEMENT</tspan></text></g>
    <g class="node" transform="translate(395 343)"><circle r="34"/><text class="sm" y="-1">SALES ORDER<tspan x="0" dy="9">PROCESSING</tspan></text></g>
    <g class="node" transform="translate(340 399)"><circle r="34"/><text class="md" y="-1">CREDIT<tspan x="0" dy="11">CHECK</tspan></text></g>
    <g class="node" transform="translate(266 419)"><circle r="34"/><text class="sm" y="-1">ORDER<tspan x="0" dy="10">FULFILLMENT</tspan></text></g>
    <g class="node" transform="translate(191 399)"><circle r="34"/><text class="md" y="3">BILLING</text></g>
    <g class="node" transform="translate(135 344)"><circle r="34"/><text class="md" y="-1">CUSTOMER<tspan x="0" dy="11">SERVICE</tspan></text></g>
    <g class="node" transform="translate(115 269)"><circle r="34"/><text class="md" y="-1">CASH<tspan x="0" dy="11">COLLECTION</tspan></text></g>
    <g class="node" transform="translate(135 194)"><circle r="34"/><text class="sm" y="-7">RECEIPT &amp;<tspan x="0" dy="10">ALLOCATION</tspan><tspan x="0" dy="10">OF CASH</tspan></text></g>
    <g class="node" transform="translate(189 139)"><circle r="34"/><text class="sm" y="-1">CASH<tspan x="0" dy="9">MANAGEMENT</tspan></text></g>
  </g>

  <!-- Supply chain management -->
  <g class="cycle supply">
    <g class="spokes">
      <line class="spoke" x1="929" y1="272" x2="929" y2="111"/>
      <line class="spoke" x1="929" y1="272" x2="1021" y2="141"/>
      <line class="spoke" x1="929" y1="272" x2="1078" y2="219"/>
      <line class="spoke" x1="929" y1="272" x2="1079" y2="315"/>
      <line class="spoke" x1="929" y1="272" x2="1023" y2="394"/>
      <line class="spoke" x1="929" y1="272" x2="932" y2="425"/>
      <line class="spoke" x1="929" y1="272" x2="839" y2="398"/>
      <line class="spoke" x1="929" y1="272" x2="781" y2="321"/>
      <line class="spoke" x1="929" y1="272" x2="777" y2="224"/>
      <line class="spoke" x1="929" y1="272" x2="832" y2="144"/>
    </g>
    <circle class="hub-ring" cx="929" cy="272" r="97"/>
    <circle class="hub-core" cx="929" cy="272" r="88"/>
    <text class="hub-title" x="929" y="268">SUPPLY CHAIN</text>
    <text class="hub-title" x="929" y="288">MANAGEMENT</text>

    <g class="node" transform="translate(929 111)"><circle r="39"/><text class="lg" y="-8">SUPPLY<tspan x="0" dy="13">CHAIN</tspan><tspan x="0" dy="13">STRATEGY</tspan></text></g>
    <g class="node" transform="translate(1021 141)"><circle r="39"/><text class="sm" y="-7">PRODUCT<tspan x="0" dy="10">RANGE</tspan><tspan x="0" dy="10">MANAGEMENT</tspan></text></g>
    <g class="node" transform="translate(1078 219)"><circle r="39"/><text class="md" y="3">FORECASTING</text></g>
    <g class="node" transform="translate(1079 315)"><circle r="39"/><text class="md" y="-1">SALES ORDER<tspan x="0" dy="11">FORECASTING</tspan></text></g>
    <g class="node" transform="translate(1023 394)"><circle r="39"/><text class="md" y="-1">PRODUCTION<tspan x="0" dy="12">SCHEDULING</tspan></text></g>
    <g class="node" transform="translate(932 425)"><circle r="39"/><text class="lg" y="-8">RAW<tspan x="0" dy="13">MATERIAL</tspan><tspan x="0" dy="13">PLANNING</tspan></text></g>
    <g class="node" transform="translate(839 398)"><circle r="39"/><text class="md" y="-1">PRODUCTION<tspan x="0" dy="12">PLANNING</tspan></text></g>
    <g class="node" transform="translate(781 321)"><circle r="39"/><text class="md" y="3">PRODUCTION</text></g>
    <g class="node" transform="translate(777 224)"><circle r="39"/><text class="sm" y="3">WAREHOUSING</text></g>
    <g class="node" transform="translate(832 144)"><circle r="39"/><text class="md" y="3">DISTRIBUTION</text></g>
  </g>

  <!-- Expenditure management -->
  <g class="cycle expenditure">
    <g class="spokes">
      <line class="spoke" x1="600" y1="836" x2="601" y2="675"/>
      <line class="spoke" x1="600" y1="836" x2="692" y2="704"/>
      <line class="spoke" x1="600" y1="836" x2="749" y2="782"/>
      <line class="spoke" x1="600" y1="836" x2="750" y2="879"/>
      <line class="spoke" x1="600" y1="836" x2="694" y2="958"/>
      <line class="spoke" x1="600" y1="836" x2="603" y2="989"/>
      <line class="spoke" x1="600" y1="836" x2="511" y2="961"/>
      <line class="spoke" x1="600" y1="836" x2="451" y2="883"/>
      <line class="spoke" x1="600" y1="836" x2="449" y2="787"/>
      <line class="spoke" x1="600" y1="836" x2="503" y2="708"/>
    </g>
    <circle class="hub-ring" cx="600" cy="836" r="96"/>
    <circle class="hub-core" cx="600" cy="836" r="88"/>
    <text class="hub-title" x="600" y="832">EXPENDITURE</text>
    <text class="hub-title" x="600" y="852">MANAGEMENT</text>

    <g class="node" transform="translate(601 675)"><circle r="39"/><text class="md" y="-1">PURCHASING<tspan x="0" dy="11">STRATEGY</tspan></text></g>
    <g class="node" transform="translate(692 704)"><circle r="39"/><text class="md" y="-1">BUDGETING &amp;<tspan x="0" dy="11">FORECASTING</tspan></text></g>
    <g class="node" transform="translate(749 782)"><circle r="39"/><text class="sm" y="-1">ORIGINATING<tspan x="0" dy="10">REQUIREMENTS</tspan></text></g>
    <g class="node" transform="translate(750 879)"><circle r="39"/><text class="md" y="-1">SELECTING &amp;<tspan x="0" dy="11">NEGOTIATING</tspan></text></g>
    <g class="node" transform="translate(694 958)"><circle r="39"/><text class="md" y="-1">ORDERING &amp;<tspan x="0" dy="11">CONTRACTING</tspan></text></g>
    <g class="node" transform="translate(603 989)"><circle r="39"/><text class="md" y="-1">RECEIVING &amp;<tspan x="0" dy="11">EVALUATING</tspan></text></g>
    <g class="node" transform="translate(511 961)"><circle r="39"/><text class="sm" y="-1">DISCREPANCY<tspan x="0" dy="10">MANAGEMENT</tspan></text></g>
    <g class="node" transform="translate(451 883)"><circle r="39"/><text class="md" y="-1">INVOICE<tspan x="0" dy="11">PROCESSING</tspan></text></g>
    <g class="node" transform="translate(449 787)"><circle r="39"/><text class="md" y="-1">PAYMENT<tspan x="0" dy="12">ISSUANCE</tspan></text></g>
    <g class="node" transform="translate(503 708)"><circle r="39"/><text class="sm" y="-1">CASH<tspan x="0" dy="10">MANAGEMENT</tspan></text></g>
  </g>

  <!-- Working capital triangle -->
  <g class="triangle">
    <polygon class="wedge" points="600,353 409,543 790,543"/>
    <path class="wedge-divider" d="M600 353 V465 M409 543 L600 465 L790 543"/>
    <text class="wedge-label" transform="translate(560 445) rotate(-45)">A/R</text>
    <text class="wedge-label" transform="translate(664 447) rotate(45)">INVENTORY</text>
    <text class="wedge-label" x="600" y="518">A/P</text>
  </g>

  <!-- Direction pointers -->
  <g class="pointers">
    <line class="pointer" x1="502" y1="429" x2="478" y2="407"/>
    <polygon class="pointer-head" points="470,399 492,404 482,408 477,418"/>
    <line class="pointer" x1="706" y1="429" x2="730" y2="407"/>
    <polygon class="pointer-head" points="738,399 716,404 726,408 731,418"/>
    <line class="pointer" x1="607" y1="560" x2="607" y2="592"/>
    <polygon class="pointer-head" points="607,604 595,581 607,589 619,581"/>
  </g>

  <!-- Cycle labels -->
  <text class="cycle-label" x="265" y="525">CUSTOMER TO CASH</text>
  <text class="cycle-label" x="929" y="525">FORECAST TO FULFILLMENT</text>
  <text class="cycle-label" x="599" y="1092">PURCHASE TO PAY</text>
</svg>
</body>
</html>
```